Membership Based Medical Practice Website

We need a functioning website for a new Membership based medical practice. There will be an enrollment fee and a monthly fee. We would like to see designs that are modern, simple. Should use neutral light colors. Examples of sites we like are www.kellanmoorclinic.com and https://fernholtcare.com/ We also have a link that when "Join Now" is clicked it will go to the signup website.

Target Market(s)

Gay Men, local population, Age group 20 to 60's.

Industry/Entity Type

Medical

Coding

Coded - Design and coding required

Number of Pages Required

5+ page

Font styles to use
Sans Serif

Colors
ffffff
cee9f5
ecf7fb
cfeae6
edf8f6
aaaaaa
e9e9e9
dbdbdb
fff3d1

Requirements
Must have
• Logo and header on every page. Clean, simple design, clear content, mobile compatible.
• Must use Wordpress
Nice to have
• Ideas should come from kellanmoorclinic.com
• Easy to read
Should not have
• Generic patient pictures, bold colors.
• Should not copy from above websites.

```html
<!DOCTYPE html>
<html lang="en">
<head>
<meta charset="utf-8">
<title>Larkfield Infectious Disease Specialists</title>
<link href="https://fonts.googleapis.com/css2?family=Source+Sans+3:wght@400;600;700&family=Poppins:wght@400;500;600&display=swap" rel="stylesheet">
<style>
:root{
  --white:#ffffff;
  --cream:#fff3d1;
  --cream-line:#f1dfa8;
  --mint:#cfeae6;
  --mint-soft:#edf8f6;
  --sky:#cee9f5;
  --sky-soft:#ecf7fb;
  --grey:#aaaaaa;
  --grey-light:#e9e9e9;
  --grey-mid:#dbdbdb;
  --ink:#222222;
  --text:#333333;
  --footer:#262626;
}
*{box-sizing:border-box;margin:0;padding:0}
html,body{width:1200px;height:4245px;overflow:hidden}
body{font-family:"Poppins",sans-serif;color:var(--text);background:var(--white);position:relative}
.abs{position:absolute}
.heading{font-family:"Source Sans 3",sans-serif}

.topbar{top:0;left:0;width:1200px;height:37px;background:var(--grey);color:var(--ink);font-size:13px;display:flex;align-items:center;padding:0 96px;justify-content:space-between}
.topbar .contact{display:flex;gap:18px;align-items:center}
.topbar .social{display:flex;gap:10px}
.topbar .social span{width:12px;height:12px;border-radius:50%;background:var(--ink);display:block}

.header{top:37px;left:0;width:1200px;height:121px;background:var(--cream);display:flex;align-items:center;justify-content:space-between;padding:0 96px}
.brand{display:flex;align-items:center;gap:12px;font-family:"Source Sans 3",sans-serif;color:#8a7a4f;font-size:14px;letter-spacing:2px;text-transform:uppercase;line-height:1.3}
.brand .mark{width:34px;height:34px;border-radius:50%;background:#ecd9a0;flex:none}
.nav{display:flex;gap:22px;font-size:16px;color:var(--ink)}

.hero{top:158px;left:0;width:1200px;height:564px;background:linear-gradient(180deg,#7e8286 0%,#a7abaf 35%,#5d6358 70%,#3a3e34 100%)}
.hero h1{position:absolute;top:150px;width:100%;text-align:center;color:var(--white);font-family:"Source Sans 3",sans-serif;font-weight:700;font-size:52px;line-height:66px}
.btn-outline{position:absolute;top:310px;left:524px;width:152px;height:48px;border:2px solid var(--white);border-radius:24px;color:var(--white);font-size:17px;display:flex;align-items:center;justify-content:center}
.badge{top:662px;left:540px;width:120px;height:120px;border-radius:50%;background:var(--white);box-shadow:0 4px 14px rgba(0,0,0,.15);display:flex;align-items:center;justify-content:center}
.badge span{width:52px;height:52px;border-radius:50%;background:var(--cream)}

.intro-title{top:872px;width:1200px;text-align:center;font-size:28px;font-weight:600;color:var(--ink)}
.intro-sub{top:936px;width:1200px;text-align:center;font-size:19px;color:var(--ink)}
.hex{width:320px;height:285px}
.hex svg{position:absolute;top:0;left:0}
.hex .label{position:absolute;top:168px;left:40px;width:240px;text-align:center;font-size:15px;line-height:28px;color:var(--ink)}
.hex .label.bold{font-weight:600}
.hex .icon{position:absolute;top:68px;left:125px}
.btn-grey{width:187px;height:57px;border-radius:29px;background:var(--grey);color:var(--white);font-size:19px;font-weight:500;display:flex;align-items:center;justify-content:center}

.benefits{top:1921px;left:0;width:1200px;height:1229px;background:var(--grey-light)}
.benefits .title{top:94px;width:1200px;text-align:center;font-size:28px;font-weight:600;color:var(--ink)}
.benefits .sub{top:148px;width:1200px;text-align:center;font-size:19px;color:var(--ink)}
.feature{width:330px;text-align:center}
.feature .disc{position:relative;margin:0 auto;width:152px;height:152px;border-radius:50%;background:var(--mint);display:flex;align-items:center;justify-content:center}
.feature .num{position:absolute;width:30px;height:30px;border-radius:50%;background:var(--sky-soft);color:#4a6b8a;font-size:12px;font-weight:600;display:flex;align-items:center;justify-content:center}
.feature .arc{position:absolute;top:-16px;left:-16px}
.feature h3{margin-top:44px;font-family:"Source Sans 3",sans-serif;font-weight:700;font-size:23px;letter-spacing:.3px;color:var(--ink)}
.feature p{margin:12px auto 0;width:270px;font-size:15px;line-height:22px;font-weight:500;color:var(--ink)}
.divider{width:1px;height:110px;background:var(--grey)}

.pricing-lead{top:3244px;left:96px;width:470px;font-size:32px;line-height:40px;font-weight:600;color:var(--ink)}
.pricing-plan{top:3334px;left:96px;width:600px;font-size:34px;line-height:42px;font-weight:600;color:var(--ink)}
.pricing-list{top:3440px;left:96px;width:620px;list-style:none;font-size:15px;line-height:22px;color:var(--ink)}
.pricing-list li{position:relative;padding-left:24px;margin-bottom:24px}
.pricing-list li::before{content:"";position:absolute;left:4px;top:9px;width:6px;height:6px;border-radius:50%;background:var(--ink)}
.btn-learn{top:3718px;left:96px;width:312px;height:57px;border-radius:29px;background:var(--grey);color:var(--white);font-size:19px;font-weight:500;display:flex;align-items:center;justify-content:center}
.photo-ring{top:3250px;left:650px;width:460px;height:460px;border-radius:50%;background:var(--grey-mid);padding:10px}
.photo{width:100%;height:100%;border-radius:50%;background:radial-gradient(circle at 45% 45%,#e9e9e9 0%,#8a8f93 30%,#3a2e2b 60%,#6a1a1a 100%)}

.footer{top:3820px;left:0;width:1200px;height:425px;background:var(--footer);color:var(--white)}
.footer .brand-f{position:absolute;top:110px;left:96px;width:290px;text-align:center;font-family:"Source Sans 3",sans-serif;font-size:16px;letter-spacing:3px;text-transform:uppercase;line-height:24px;color:#dddddd}
.footer .brand-f .mark{width:60px;height:60px;border-radius:50%;border:2px solid #dddddd;margin:0 auto 16px}
.footer h4{font-family:"Source Sans 3",sans-serif;font-size:20px;font-weight:700;margin-bottom:28px}
.footer .col{position:absolute;top:68px;font-size:14px}
.contact-row{display:flex;gap:14px;margin-bottom:20px;line-height:20px;width:250px}
.contact-row .ico{flex:none;width:28px;height:28px;border:1.5px solid var(--white);border-radius:50%;display:flex;align-items:center;justify-content:center}
.menu li{list-style:none;line-height:28px}
.social-row{display:flex;align-items:center;gap:12px;margin-bottom:10px}
.social-row span{width:26px;height:26px;border-radius:50%;border:1.5px solid var(--white)}
.copyright{position:absolute;top:370px;width:1200px;text-align:center;font-size:13px}
</style>
</head>
<body>

<div class="abs topbar">
  <div class="contact">
    <span>&#9742; 888 888 8888</span><span>|</span><span>&#9993; info@larkfieldid.com</span>
  </div>
  <div class="social"><span></span><span></span><span></span><span></span></div>
</div>

<header class="abs header">
  <div class="brand"><span class="mark"></span><span>Larkfield<br>Infectious Disease Specialists</span></div>
  <nav class="nav"><span>Home</span><span>About Us</span><span>Specialties</span><span>Pricing</span><span>FAQ</span><span>Blog</span><span>Contact Us</span></nav>
</header>

<section class="abs hero" role="img" aria-label="Misty mountain road stretching into the distance">
  <h1>Specialty medicine with Commitment,<br>Compassion and Care</h1>
  <div class="btn-outline">Join Us</div>
</section>
<div class="abs badge"><span></span></div>

<h2 class="abs intro-title heading">We offer comprehensive treatment of a wide variety of infectious diseases.</h2>
<p class="abs intro-sub">Out expertise is in the following area.</p>

<div class="abs hex" style="top:1047px;left:95px">
  <svg width="320" height="285" viewBox="0 0 320 285"><polygon points="2,142 80,4 240,4 318,142 240,281 80,281" fill="none" stroke="var(--cream-line)" stroke-width="3"/><polygon points="18,142 90,16 230,16 302,142 230,269 90,269" fill="var(--cream)" stroke="#e9d9a6" stroke-width="2"/></svg>
  <svg class="icon" width="70" height="70" viewBox="0 0 60 60" fill="none" stroke="#222" stroke-width="2.5"><circle cx="30" cy="30" r="16"/><circle cx="24" cy="26" r="3"/><circle cx="35" cy="34" r="3"/><path d="M30 6v8M30 46v8M6 30h8M46 30h8M13 13l6 6M41 41l6 6M13 47l6-6M41 19l6-6"/></svg>
  <div class="label">HIV/PrEP</div>
</div>
<div class="abs hex" style="top:1047px;left:437px">
  <svg width="320" height="285" viewBox="0 0 320 285"><polygon points="2,142 80,4 240,4 318,142 240,281 80,281" fill="none" stroke="var(--cream-line)" stroke-width="3"/><polygon points="18,142 90,16 230,16 302,142 230,269 90,269" fill="#f6f8fb" stroke="#d8d8d8" stroke-width="2"/></svg>
  <svg class="icon" width="70" height="70" viewBox="0 0 60 60" fill="none" stroke="#222" stroke-width="2.5"><path d="M20 48C8 40 10 18 26 14c14-3 22 10 16 20-4 7-14 6-14-2 0-6 8-7 8-2"/><path d="M40 12c12 8 10 30-6 34"/></svg>
  <div class="label bold">Chronic Hepatitis</div>
</div>
<div class="abs hex" style="top:1047px;left:782px">
  <svg width="320" height="285" viewBox="0 0 320 285"><polygon points="2,142 80,4 240,4 318,142 240,281 80,281" fill="none" stroke="var(--cream-line)" stroke-width="3"/><polygon points="18,142 90,16 230,16 302,142 230,269 90,269" fill="#f6f8fb" stroke="#d8d8d8" stroke-width="2"/></svg>
  <svg class="icon" width="70" height="70" viewBox="0 0 60 60" fill="none" stroke="#222" stroke-width="2.5"><circle cx="24" cy="30" r="9"/><path d="M24 39v14M18 47h12M31 23l12-12M36 11h7v7"/><circle cx="40" cy="24" r="5"/></svg>
  <div class="label bold">Sexually transmitted<br>infections</div>
</div>
<div class="abs hex" style="top:1395px;left:95px">
  <svg width="320" height="285" viewBox="0 0 320 285"><polygon points="2,142 80,4 240,4 318,142 240,281 80,281" fill="none" stroke="var(--cream-line)" stroke-width="3"/><polygon points="18,142 90,16 230,16 302,142 230,269 90,269" fill="#f6f8fb" stroke="#d8d8d8" stroke-width="2"/></svg>
  <svg class="icon" width="70" height="70" viewBox="0 0 60 60" fill="none" stroke="#222" stroke-width="2.5"><rect x="14" y="30" width="32" height="24" rx="3"/><path d="M22 30v-6h16v6"/><path d="M30 36v12M24 42h12"/><rect x="40" y="6" width="14" height="10"/></svg>
  <div class="label bold">Pre-travel vaccinations<br>and counselling</div>
</div>
<div class="abs hex" style="top:1395px;left:437px">
  <svg width="320" height="285" viewBox="0 0 320 285"><polygon points="2,142 80,4 240,4 318,142 240,281 80,281" fill="none" stroke="var(--cream-line)" stroke-width="3"/><polygon points="18,142 90,16 230,16 302,142 230,269 90,269" fill="#f6f8fb" stroke="#d8d8d8" stroke-width="2"/></svg>
  <svg class="icon" width="70" height="70" viewBox="0 0 60 60" fill="none" stroke="#222" stroke-width="2.5"><rect x="18" y="8" width="20" height="22" rx="10"/><path d="M8 56c0-14 10-20 20-20s20 6 20 20z"/><path d="M48 14v18M44 20h8"/></svg>
  <div class="label">Infections associated<br>with medical devices</div>
</div>
<div class="abs hex" style="top:1395px;left:782px">
  <svg width="320" height="285" viewBox="0 0 320 285"><polygon points="2,142 80,4 240,4 318,142 240,281 80,281" fill="none" stroke="var(--cream-line)" stroke-width="3"/><polygon points="18,142 90,16 230,16 302,142 230,269 90,269" fill="#f6f8fb" stroke="#d8d8d8" stroke-width="2"/></svg>
  <svg class="icon" width="70" height="70" viewBox="0 0 60 60" fill="none" stroke="#222" stroke-width="2.5"><path d="M20 40L40 20"/><circle cx="44" cy="12" r="5"/><circle cx="50" cy="20" r="5"/><circle cx="10" cy="42" r="5"/><circle cx="18" cy="50" r="5"/></svg>
  <div class="label bold">Bone and Joint<br>infections.</div>
</div>

<div class="abs btn-grey" style="top:1772px;left:506px">View More</div>

<section class="abs benefits">
  <h2 class="abs title heading">Less wait, more personal.</h2>
  <p class="abs sub">We are not your traditional doctor’s office.</p>

  <div class="abs feature" style="top:273px;left:90px">
    <div class="disc">
      <svg class="arc" width="184" height="184" viewBox="0 0 184 184"><path d="M92 4a88 88 0 0 1 88 88" fill="none" stroke="var(--sky)" stroke-width="2"/></svg>
      <span class="num" style="left:-30px;top:10px">01</span>
      <svg width="70" height="70" viewBox="0 0 70 70" fill="none" stroke="#222" stroke-width="3"><circle cx="35" cy="35" r="28"/><path d="M43 25c-2-3-5-4-8-4-5 0-8 3-8 6 0 8 17 5 17 14 0 4-4 7-9 7-4 0-7-2-9-5M35 16v5M35 48v6"/></svg>
    </div>
    <h3>STRAIGHTFORWARD PRICING</h3>
    <p>We charge all our patients the same low rate - no surprises.</p>
  </div>
  <div class="abs divider" style="top:510px;left:427px"></div>
  <div class="abs feature" style="top:273px;left:432px">
    <div class="disc">
      <svg class="arc" width="184" height="184" viewBox="0 0 184 184"><path d="M4 92a88 88 0 0 0 88 88" fill="none" stroke="var(--sky)" stroke-width="2"/></svg>
      <span class="num" style="left:-18px;top:104px">02</span>
      <svg width="70" height="70" viewBox="0 0 70 70" fill="none" stroke="#222" stroke-width="3"><ellipse cx="35" cy="14" rx="12" ry="5"/><path d="M23 14v14c0 3 5 5 12 5s12-2 12-5V14M23 21c0 3 5 5 12 5s12-2 12-5"/><path d="M6 46l14-6 16 4 22-6c4 0 4 5 0 6L36 54H18l-12 6"/></svg>
    </div>
    <h3>AVAILABLE WHEN YOU ARE</h3>
    <p>New patient appointments are available within 1 week.</p>
  </div>
  <div class="abs divider" style="top:510px;left:770px"></div>
  <div class="abs feature" style="top:273px;left:777px">
    <div class="disc">
      <svg class="arc" width="184" height="184" viewBox="0 0 184 184"><path d="M4 92a88 88 0 0 1 88-88" fill="none" stroke="var(--sky)" stroke-width="2"/></svg>
      <span class="num" style="left:-30px;top:10px">03</span>
      <svg width="70" height="70" viewBox="0 0 70 70" fill="none" stroke="#222" stroke-width="3"><rect x="14" y="8" width="42" height="54" rx="3"/><path d="M20 8v54M27 46l8-22 8 22M30 38h10"/></svg>
    </div>
    <h3>HASSLE-FREE BOOKING</h3>
    <p>Schedule your appointment online at your convenience - no need to call during business hours.</p>
  </div>

  <div class="abs feature" style="top:677px;left:90px">
    <div class="disc">
      <svg class="arc" width="184" height="184" viewBox="0 0 184 184"><path d="M92 4a88 88 0 0 1 88 88" fill="none" stroke="var(--sky)" stroke-width="2"/></svg>
      <span class="num" style="left:-30px;top:10px">04</span>
      <svg width="70" height="70" viewBox="0 0 70 70" fill="none" stroke="#222" stroke-width="3"><path d="M8 58l10-22 12-4 16 10M10 34l26-18 24 18v22H22"/><path d="M40 34h10v10H40z"/></svg>
    </div>
    <h3>DEVOTED CARE</h3>
    <p>We schedule enough time at each visit to make sure all of your questions are answered.</p>
  </div>
  <div class="abs divider" style="top:914px;left:427px"></div>
  <div class="abs feature" style="top:677px;left:432px">
    <div class="disc">
      <svg class="arc" width="184" height="184" viewBox="0 0 184 184"><path d="M4 92a88 88 0 0 0 88 88" fill="none" stroke="var(--sky)" stroke-width="2"/></svg>
      <span class="num" style="left:-18px;top:104px">05</span>
      <svg width="70" height="70" viewBox="0 0 70 70" fill="none" stroke="#222" stroke-width="3"><path d="M8 46h54v-8l-8-4-6-10H22l-6 10-8 4z"/><circle cx="20" cy="48" r="5"/><circle cx="50" cy="48" r="5"/><path d="M30 12v8M40 12v8M28 16h14"/></svg>
    </div>
    <h3>WITHIN YOUR REACH</h3>
    <p>Follow-up appointments may be done by video chat for your convenience.</p>
  </div>
  <div class="abs divider" style="top:914px;left:770px"></div>
  <div class="abs feature" style="top:677px;left:777px">
    <div class="disc">
      <svg class="arc" width="184" height="184" viewBox="0 0 184 184"><path d="M4 92a88 88 0 0 1 88-88" fill="none" stroke="var(--sky)" stroke-width="2"/></svg>
      <span class="num" style="left:-30px;top:10px">06</span>
      <svg width="70" height="70" viewBox="0 0 70 70" fill="none" stroke="#222" stroke-width="3"><rect x="14" y="8" width="30" height="46"/><path d="M20 18h18M20 26h18M20 34h10"/><rect x="32" y="32" width="24" height="30"/><path d="M37 40h14M37 48h4M45 48h4M37 55h4M45 55h4"/></svg>
    </div>
    <h3>SAVE ON LAB COSTS</h3>
    <p>If paying upfront for labs, we offer discounted pricing of up to 90% off standard rates.</p>
  </div>

  <div class="abs btn-grey" style="top:1083px;left:506px">View More</div>
</section>

<h2 class="abs pricing-lead heading">Our pricing is simple, transparent and affordable.</h2>
<h3 class="abs pricing-plan heading">Membership Plan $80/mo,<br>plus a one-time $99 enrollment fee.</h3>
<ul class="abs pricing-list">
  <li>Includes all appointments, no co-pay</li>
  <li>Relaxed, unrushed visits</li>
  <li>Direct communication with your doctor via phone, email,<br>video chat 24/7</li>
  <li>Convenient online scheduling (no need to call during business hours)</li>
  <li>Wholesale price for labs and medications</li>
</ul>
<div class="abs btn-learn">Learn More About us</div>
<div class="abs photo-ring"><div class="photo" role="img" aria-label="Hand holding an enamel camping mug with a snowy outdoor backdrop"></div></div>

<footer class="abs footer">
  <div class="brand-f"><div class="mark"></div>Larkfield<br><span style="font-size:13px;letter-spacing:1px">Infectious Disease Specialists</span></div>
  <div class="col" style="left:433px">
    <h4>CONTACT US</h4>
    <div class="contact-row"><span class="ico"><svg width="14" height="14" viewBox="0 0 14 14" fill="none" stroke="#fff" stroke-width="1.5"><path d="M7 13s-4-4.5-4-7.5a4 4 0 0 1 8 0C11 8.5 7 13 7 13z"/><circle cx="7" cy="5.5" r="1.5"/></svg></span><span>Address :<br>Lorem Ipsum is simply dummy text of the printing and typesetting industry.</span></div>
    <div class="contact-row"><span class="ico"><svg width="14" height="14" viewBox="0 0 14 14" fill="none" stroke="#fff" stroke-width="1.5"><path d="M3 1l2 3-1.5 1.5a8 8 0 0 0 5 5L10 9l3 2-1.5 2C6 13 1 8 1 2.5z"/></svg></span><span>Call Us :<br>888 888 8888</span></div>
    <div class="contact-row"><span class="ico"><svg width="14" height="14" viewBox="0 0 14 14" fill="none" stroke="#fff" stroke-width="1.5"><rect x="1" y="3" width="12" height="8"/><path d="M1 3l6 5 6-5"/></svg></span><span>E - Mail :<br>info@larkfieldid.com</span></div>
  </div>
  <div class="col" style="left:747px">
    <h4>MENU</h4>
    <ul class="menu"><li>Home</li><li>About US</li><li>Specialties</li><li>Pricing</li><li>FAQ</li><li>Contact US</li></ul>
  </div>
  <div class="col" style="left:934px">
    <h4>GET IN TOUCH</h4>
    <div class="social-row"><span></span>Newsletter</div>
    <div class="social-row"><span></span>Community</div>
    <div class="social-row"><span></span>Events</div>
    <div class="social-row"><span></span>Gallery</div>
  </div>
  <p class="copyright">© 2019 Copyrights | All Rights Reserved</p>
</footer>

</body>
</html>
```